Website Design for Forklift Training Company

DO NOT CONTACT PRIVATELY. ONLY SUBMISSIONS HERE WILL BE CONSIDERED

I need a design for a website that offers forklift training courses.

The company offers accredited, onsite forklift training that are customized for the needs of each individual company. The company offers a variety of courses to operate forklifts and other machinary.

About: "KVW Training Ltd delivers bespoke onsite forklift truck operator training throught the uk.
All our instructors have a wealth of knowledge and expertise to provide your company with all your forklift truck training requirements.
KVW Training Ltd is registered and accredited by plomvex standards so you can be rest assured that all forklift training is carried out the very highest standard"

I need the following pages designed:
> a) Home Page: Include a header image, ways to contact, about snippet, overview of courses, accreditation that will be received after completing the courses. (See attachments for samples)
> b) About Page
> c) Contact Us Page
> d) Course Page Template: A page that will be used as template for the courses offered. It should contain;
1. Cover image for the course
2. A description of the course
3. A table indicating the various course options
4. Course Objectives
5. What the trainee will receive after doing the course (example: a certification)

Industrial Businesses

4 page

Colors
0054AA
0677BA
7BADD7
CADEEF
E8F1F8
0094D4
00A9DD
6FCCEA
C7EBF8
E9F6FB

• - No Search bar

```html
<!DOCTYPE html>
<html lang="en">
<head>
<meta charset="utf-8">
<title>Contact Us – KVW Training Ltd</title>
<link rel="stylesheet" href="https://fonts.googleapis.com/css2?family=Montserrat:wght@300;400;600;700&family=Oswald:wght@300;400&family=Roboto:wght@400&display=swap">
<style>
:root{
  --blue-deep:#0054AA;
  --blue-mid:#0677BA;
  --blue-soft:#7BADD7;
  --blue-pale:#E8F1F8;
  --cyan:#0094D4;
  --cyan-bright:#00A9DD;
  --navy:#0b2a5b;
  --footer:#023f8a;
  --ink:#222;
  --muted:#6b6b6b;
  --line:#c9c9c9;
  --white:#fff;
}
*{margin:0;padding:0;box-sizing:border-box}
html,body{width:965px;height:1200px;overflow:hidden}
body{position:relative;background:var(--blue-pale);font-family:'Montserrat',sans-serif;color:var(--ink)}
.abs{position:absolute;line-height:1;white-space:nowrap}

/* hero */
.hero{position:absolute;left:0;top:0;width:965px;height:418px;overflow:hidden}
.hero svg{position:absolute;left:0;top:0}
.brand{left:71px;top:46px;font-weight:600;font-size:12.5px;color:var(--white);letter-spacing:.3px}
.brand-mark{left:112px;top:6px;width:30px;height:30px;border:2px solid var(--white);border-radius:50%}
.nav a{position:absolute;top:20px;font-family:'Oswald',sans-serif;font-size:15px;color:var(--white);text-decoration:none;line-height:1}
.nav .active::after{content:"";position:absolute;left:2px;right:2px;top:22px;height:2px;background:var(--white)}
.hero-kicker{left:68px;top:179px;font-weight:300;font-size:19px;letter-spacing:1.5px;color:var(--white)}
.hero-title{left:66px;top:209px;font-weight:700;font-size:36px;color:var(--white)}

/* intro */
.eyebrow{left:0;width:949px;text-align:center;top:456px;font-family:'Oswald',sans-serif;font-size:15px;letter-spacing:2.5px;color:#1d3f6e}
.headline{left:0;width:960px;text-align:center;top:476px;font-weight:700;font-size:28px;color:var(--navy)}
.headline span{color:var(--cyan)}
.headline-rule{left:448px;top:511px;width:64px;height:3px;background:var(--cyan)}
.intro{left:190px;width:585px;top:526px;font-size:11px;line-height:18.6px;color:#333;text-align:center;white-space:normal}

/* contact info card */
.info-card{left:114px;top:602px;width:323px;height:277px;background:linear-gradient(150deg,#12c3f2 0%,#0a8fd3 45%,var(--blue-deep) 100%)}
.info-title{left:151px;top:646px;font-family:'Oswald',sans-serif;font-size:20px;color:var(--white)}
.icon-ring{width:40px;height:40px;border:2px solid var(--white);border-radius:50%;display:flex;align-items:center;justify-content:center}
.info-label{font-family:'Oswald',sans-serif;font-weight:300;font-size:12px;color:var(--white)}
.info-value{font-weight:700;font-size:12px;color:var(--white)}
.forklift{left:99px;top:812px;width:238px;height:174px;background:linear-gradient(160deg,#3a3f45 0%,#6b6f73 40%,#e8b73a 70%,#f3c94a 100%);border-radius:10px 30px 6px 6px;opacity:.9}

/* form */
.form-frame{left:576px;top:619px;width:264px;height:251px;border:2px solid var(--blue-mid)}
.form-card{left:369px;top:639px;width:452px;height:312px;background:var(--white);box-shadow:0 4px 18px rgba(0,60,120,.12)}
.form-title{left:407px;top:670px;font-weight:600;font-size:17px;color:#1c1c1c}
.field-label{font-family:'Roboto',sans-serif;font-size:10.5px;color:#1c1c1c}
.field-value{font-family:'Roboto',sans-serif;font-size:9px;color:var(--muted)}
.field-line{height:1px;background:var(--line)}
.send{left:733px;top:874px;width:46px;height:46px;border-radius:50%;background:var(--cyan-bright);display:flex;align-items:center;justify-content:center}

/* footer */
.footer{left:0;top:1056px;width:965px;height:144px;background:var(--footer)}
.footer-nav a{position:absolute;top:1092px;font-family:'Oswald',sans-serif;font-size:14px;color:var(--white);text-decoration:none;line-height:1}
.copyright{left:0;width:962px;text-align:center;top:1123px;font-family:'Roboto',sans-serif;font-size:9.5px;color:#b8c8e6}
.social{top:1144px;width:20px;height:20px;border-radius:50%;background:var(--white)}
</style>
</head>
<body>

<header class="hero">
  <svg width="965" height="418" viewBox="0 0 965 418">
    <defs>
      <linearGradient id="heroBlue" x1="0" y1="0" x2="1" y2="1">
        <stop offset="0" stop-color="#0a6fc4"/>
        <stop offset=".6" stop-color="#0558ad"/>
        <stop offset="1" stop-color="#063d8a"/>
      </linearGradient>
      <linearGradient id="officeTone" x1="0" y1="0" x2="1" y2="1">
        <stop offset="0" stop-color="#e6e8ea"/>
        <stop offset=".5" stop-color="#c9ccce"/>
        <stop offset="1" stop-color="#5a5d62"/>
      </linearGradient>
    </defs>
    <rect width="965" height="418" fill="url(#heroBlue)" role="img" aria-label="Warehouse with forklift under a blue tint"/>
    <path d="M540 418 C600 260 680 120 780 0 L965 0 L965 418 Z" fill="url(#officeTone)" role="img" aria-label="Smiling support agent wearing a headset at an office desk"/>
    <path d="M508 418 C570 250 650 110 745 0" fill="none" stroke="#ffffff" stroke-width="2"/>
    <path d="M523 418 C585 250 668 110 760 0" fill="none" stroke="#1f86d6" stroke-width="3"/>
  </svg>
  <div class="abs brand-mark" aria-hidden="true"></div>
  <div class="abs brand">KVW TRAINING LTD</div>
  <nav class="nav">
    <a style="left:252px">HOME</a>
    <a style="left:334px">ABOUT US</a>
    <a style="left:441px">COURSES</a>
    <a class="active" style="left:541px">CONTACT US</a>
  </nav>
  <div class="abs hero-kicker">GET IN TOUCH</div>
  <h1 class="abs hero-title">CONTACT US</h1>
</header>

<div class="abs eyebrow">CONTAT US</div>
<h2 class="abs headline"><span>GET IN</span> TOUCH</h2>
<div class="abs headline-rule"></div>
<p class="abs intro">KVW Training Ltd delivers bespoke onsite forklift truck operator training throught the uk. All our instruc-<br>tors have a wealth of knowledge and expertise to provide your company with all</p>

<section>
  <div class="abs info-card"></div>
  <h3 class="abs info-title">CONTACT INFORMATION</h3>
  <div class="abs icon-ring" style="left:151px;top:686px">
    <svg width="18" height="18" viewBox="0 0 24 24"><path d="M6.6 10.8a15 15 0 0 0 6.6 6.6l2.2-2.2a1 1 0 0 1 1-.25 11.4 11.4 0 0 0 3.6.57 1 1 0 0 1 1 1V20a1 1 0 0 1-1 1A17 17 0 0 1 3 4a1 1 0 0 1 1-1h3.5a1 1 0 0 1 1 1c0 1.25.2 2.45.57 3.57a1 1 0 0 1-.25 1z" fill="#fff"/></svg>
  </div>
  <div class="abs info-label" style="left:201px;top:690px">PHONE NUMBER</div>
  <div class="abs info-value" style="left:201px;top:707px">(123) 456 7890</div>
  <div class="abs icon-ring" style="left:151px;top:746px">
    <svg width="18" height="14" viewBox="0 0 18 14"><rect x="1" y="1" width="16" height="12" fill="none" stroke="#fff" stroke-width="1.5"/><path d="M1 1l8 6 8-6M1 13l6-5M17 13l-6-5" fill="none" stroke="#fff" stroke-width="1.3"/></svg>
  </div>
  <div class="abs info-label" style="left:203px;top:749px">EMAIL ADDRESS</div>
  <div class="abs info-value" style="left:203px;top:767px">info@kvwtraining.com</div>
  <div class="abs forklift" role="img" aria-label="Yellow forklift truck"></div>

  <div class="abs form-frame"></div>
  <form class="abs form-card"></form>
  <h3 class="abs form-title">Send us a Message</h3>

  <div class="abs field-label" style="left:411px;top:719px">Your Name</div>
  <div class="abs field-value" style="left:411px;top:740px">Alex Morgan</div>
  <div class="abs field-line" style="left:411px;top:758px;width:164px"></div>
  <div class="abs field-label" style="left:611px;top:719px">Company</div>
  <div class="abs field-value" style="left:611px;top:741px">Lorem ipsum dolor sit amet</div>
  <div class="abs field-line" style="left:611px;top:758px;width:164px"></div>

  <div class="abs field-label" style="left:411px;top:785px">Email&nbsp; Address</div>
  <div class="abs field-value" style="left:411px;top:808px">alexmorgan@mailbox.com</div>
  <div class="abs field-line" style="left:411px;top:825px;width:164px"></div>
  <div class="abs field-label" style="left:611px;top:785px">Phone</div>
  <div class="abs field-value" style="left:611px;top:808px">01122-123-456-789</div>
  <div class="abs field-line" style="left:611px;top:825px;width:164px"></div>

  <div class="abs field-label" style="left:410px;top:853px">Message</div>
  <div class="abs field-value" style="left:411px;top:876px">Hi, do you have a moment to talk ab...!</div>
  <div class="abs field-line" style="left:412px;top:913px;width:326px"></div>
  <div class="abs send" aria-label="Send">
    <svg width="18" height="18" viewBox="0 0 24 24"><path d="M22 2L2 10l7 3 3 7z" fill="#fff"/><path d="M22 2L9 13" stroke="#00A9DD" stroke-width="1.5"/></svg>
  </div>
</section>

<footer class="abs footer"></footer>
<nav class="footer-nav">
  <a style="left:299px">HOME</a>
  <a style="left:390px">ABOUT US</a>
  <a style="left:501px">COURSES</a>
  <a style="left:609px">CONTACT US</a>
</nav>
<div class="abs copyright">2020 © COPYRIGHT DEI KVW TRAINING LTD RIGHTS RESERVED.</div>
<div class="abs social" style="left:461px" aria-label="Social link"></div>
<div class="abs social" style="left:484px" aria-label="Social link"></div>
<div class="abs social" style="left:506px" aria-label="Social link"></div>

</body>
</html>
```